Business Card Design for Occupational Medicine Start Up Company

We need to design a professional business card. We are a healthcare company providing occupational medicine services to blue collar industries. We are professional, efficient and high quality service providers.

Target Market(s)

Blue Collar Industry: Shipbuilding, Ports, Trucking Companies; The Executives and Safety Officers for these companies

Industry/Entity Type

Healthcare

Contact Information for Business Card

Logo, Name, Title, Email, Phone

Other font styles liked:
• Please match our Brand Guide

Requirements
Must have
• Our Company Colors and Logo

```html
<!DOCTYPE html>
<html lang="en">
<head>
<meta charset="utf-8">
<title>Harborline Clinics – Business Card</title>
<link href="https://fonts.googleapis.com/css2?family=Montserrat:wght@400;600&display=swap" rel="stylesheet">
<style>
  :root {
    --navy: #2a3582;
    --ink-grey: #6d6e71;
    --paper: #ffffff;
    --backdrop: #e4e4e4;
  }
  * { margin: 0; padding: 0; box-sizing: border-box; }
  html, body {
    width: 1200px;
    height: 900px;
    overflow: hidden;
    background: var(--backdrop);
    font-family: "Montserrat", sans-serif;
  }
  .card {
    position: absolute;
    left: 328px;
    width: 445px;
    height: 254px;
  }
  .card--front { top: 165px; background: var(--paper); }
  .card--back  { top: 467px; background: var(--navy); }

  /* brand lockup: one plain circle + single-weight name */
  .brand { position: absolute; display: flex; flex-direction: column; align-items: center; }
  .brand__dot { border-radius: 50%; }
  .brand__name, .brand__sub { font-weight: 600; line-height: 1; }

  .card--front .brand { right: 18px; top: 20px; width: 160px; }
  .card--front .brand__dot { width: 46px; height: 46px; background: var(--navy); margin-bottom: 10px; }
  .card--front .brand__name { color: var(--navy); font-size: 17px; letter-spacing: 0.5px; }
  .card--front .brand__sub { color: var(--navy); font-size: 10px; letter-spacing: 4px; margin-top: 6px; }

  .card--back .brand { left: 48px; top: 90px; flex-direction: row; align-items: center; gap: 30px; }
  .card--back .brand__dot { width: 76px; height: 76px; background: var(--paper); }
  .card--back .brand__text { display: flex; flex-direction: column; align-items: center; }
  .card--back .brand__name { color: var(--paper); font-size: 28px; letter-spacing: 1px; }
  .card--back .brand__sub { color: var(--paper); font-size: 15px; letter-spacing: 8px; margin-top: 8px; }

  .contact { position: absolute; left: 20px; top: 141px; }
  .contact__name { color: var(--navy); font-size: 16px; letter-spacing: 0.3px; font-weight: 400; }
  .contact__name strong { font-weight: 600; }
  .contact__title { color: var(--ink-grey); font-size: 14px; margin-top: 3px; }
  .contact__line { color: var(--ink-grey); font-size: 12.5px; }
  .contact__email { margin-top: 17px; }
  .contact__phone { margin-top: 9px; }
</style>
</head>
<body>
  <section class="card card--front">
    <div class="brand">
      <span class="brand__dot"></span>
      <span class="brand__name">HARBORLINE</span>
      <span class="brand__sub">CLINICS</span>
    </div>
    <div class="contact">
      <p class="contact__name"><strong>DANA</strong> FIELDING</p>
      <p class="contact__title">Cardiac Sonographer</p>
      <p class="contact__line contact__email">dana.fielding@harborline.com</p>
      <p class="contact__line contact__phone">555-014-2276</p>
    </div>
  </section>

  <section class="card card--back">
    <div class="brand">
      <span class="brand__dot"></span>
      <div class="brand__text">
        <span class="brand__name">HARBORLINE</span>
        <span class="brand__sub">CLINICS</span>
      </div>
    </div>
  </section>
</body>
</html>
```